Rebrand & reskin fitbrisko.com (Uncoded)

Fitbrisko.com is a commerce website and app for sports and fitness classes and events. In order to improve its appeal, we invite designers to provide their 'skins' for the landing page, club page and event page. Designers can propose using alternate controls and layouts for these pages, and comment on ways to improve the site's usability. It must remain easy to use on a portrait mobile phone screen, responsive design where necessary to also provide a good experience on desktop.

Please navigate to fitbrisko.com and explore the site, and we look forwards to your suggestions!

Target Market(s)

Primary: Tech-savvy mobile users. Secondary: Desktop users

Industry/Entity Type

Health And Wellness

Number of Pages Required

3 page

Font styles to use
Sans Serif

Colors
ffffff
f37122

Requirements
Must have
• This brief is all about changing the look and feel of the site; the winning design will have an immediate 'wow' factor, yet not sacrifice the ease of finding and paying for classes. It must retain the logo, white and orange must be the primary colours used.
Should not have
• The colour palette must remain roughly as is; for example, a very dark site will not appeal.

```html
<!DOCTYPE html>
<html lang="en">
<head>
<meta charset="utf-8">
<title>Fitbrisko – Feed</title>
<link href="https://fonts.googleapis.com/css2?family=Heebo:wght@400;500&family=Open+Sans:wght@400&display=swap" rel="stylesheet">
<style>
  :root{
    --orange:#f37122;
    --orange-light:#f58a3c;
    --orange-deep:#f05a18;
    --white:#ffffff;
    --page:#efefef;
    --ink:#3a3a3a;
    --muted:#8a8a8a;
    --line:#d6d6d6;
    --footer:#2b2b2b;
    --nav-active:#2e2e2e;
  }
  *{box-sizing:border-box;margin:0;padding:0}
  html,body{width:1200px;height:928px;overflow:hidden}
  body{position:relative;background:var(--page);font-family:"Open Sans",sans-serif;color:var(--ink)}

  .site-header{position:absolute;left:0;top:0;width:1200px;height:102px;
    background:linear-gradient(#fbfbfb,#ececec);border-bottom:1px solid #cfcfcf}
  .brand{position:absolute;left:116px;top:36px;display:flex;align-items:center;gap:10px}
  .brand-dot{width:30px;height:30px;border-radius:50%;background:var(--orange)}
  .brand-name{font-family:"Heebo",sans-serif;font-weight:500;font-size:27px;letter-spacing:1px;color:var(--orange)}

  .main-nav{position:absolute;top:0;left:0;height:102px;width:1200px}
  .main-nav a{position:absolute;top:0;height:102px;display:flex;align-items:center;justify-content:center;
    font-family:"Heebo",sans-serif;font-size:17px;color:#4a4a4a;text-decoration:none;letter-spacing:.3px}
  .nav-calendar{left:420px;width:156px}
  .nav-feed{left:576px;width:114px;background:linear-gradient(#525252,#252525);color:var(--white)!important}
  .nav-nearby{left:690px;width:137px}
  .nav-classes{left:827px;width:139px;border-left:1px solid #d2d2d2;border-right:1px solid #d2d2d2}
  .nav-event{left:966px;width:130px}

  .side-menu{position:absolute;left:105px;top:102px;width:223px;height:767px;background:var(--orange)}
  .side-menu a{display:flex;align-items:center;height:57px;padding-left:30px;gap:12px;
    border-bottom:1px solid #f58d4c;color:var(--white);text-decoration:none;
    font-family:"Heebo",sans-serif;font-weight:500;font-size:17px;letter-spacing:.3px}
  .side-menu a:first-child{height:71px;padding-top:0}
  .side-menu svg{width:28px;height:28px;flex:none}

  .content{position:absolute;left:328px;top:102px;width:768px;height:765px;background:var(--white);
    border-right:1px solid #dcdcdc}
  .welcome-title{position:absolute;left:36px;top:44px;font-family:"Heebo",sans-serif;font-weight:400;
    font-size:26px;letter-spacing:.6px;color:#333}
  .welcome-text{position:absolute;left:38px;top:84px;width:690px;font-size:16.5px;line-height:25px;color:var(--muted)}

  .day-band{position:absolute;left:36px;width:708px;height:42px;padding-left:21px;display:flex;align-items:center;
    font-family:"Heebo",sans-serif;font-weight:500;font-size:16.5px;color:var(--white);letter-spacing:.2px}
  .band-today{top:181px;background:linear-gradient(var(--orange-light),var(--orange-deep))}
  .band-tomorrow{top:512px;background:var(--orange)}

  .event-card{position:absolute;left:36px;width:708px;height:139px;background:var(--white);border:1px solid var(--line)}
  .event-date{position:absolute;left:24px;top:13px;font-family:"Heebo",sans-serif;font-size:16px;color:#777}
  .event-thumb{position:absolute;left:22px;top:47px;width:61px;height:61px;border-radius:50%}
  .event-title{position:absolute;left:96px;top:45px;font-size:15px;color:var(--orange)}
  .event-club,.event-desc{position:absolute;left:96px;font-size:12.5px;color:var(--muted)}
  .event-club{top:70px}
  .event-desc{top:91px}
  .card-1{top:223px}
  .card-2{top:362px;left:37px;width:707px}
  .card-3{top:554px}
  .thumb-badge{background:radial-gradient(circle,#a01818,#6a0d0d)}
  .thumb-athlete{background:radial-gradient(circle at 40% 40%,#c9b8a8,#5a3a2a)}
  .thumb-runner{background:radial-gradient(circle at 45% 45%,#e6c7b2,#8d6450)}

  .site-footer{position:absolute;left:0;top:869px;width:1200px;height:59px;background:var(--footer);
    display:flex;align-items:center;justify-content:center;font-size:14px;color:#bdbdbd;word-spacing:1px}
</style>
</head>
<body>
  <header class="site-header">
    <div class="brand"><span class="brand-dot"></span><span class="brand-name">FITBRISKO</span></div>
    <nav class="main-nav">
      <a class="nav-calendar" href="#">CALENDAR</a>
      <a class="nav-feed" href="#">FEED</a>
      <a class="nav-nearby" href="#">NEAR BY</a>
      <a class="nav-classes" href="#">CLASSES</a>
      <a class="nav-event" href="#">EVENT</a>
    </nav>
  </header>

  <aside class="side-menu">
    <a href="#"><svg viewBox="0 0 28 28" fill="none" stroke="#fff" stroke-width="2.4"><path d="M16 5h6a2 2 0 0 1 2 2v14a2 2 0 0 1-2 2h-6"/><path d="M3 11h7V7l7 7-7 7v-4H3z" fill="#fff" stroke="none"/></svg>LOGIN</a>
    <a href="#"><svg viewBox="0 0 28 28" fill="none" stroke="#fff" stroke-width="2"><rect x="5" y="3" width="18" height="22" rx="2"/><path d="M9 3v8l2-2 2 2V3"/><path d="M14 15l1.2 2.5 2.6.3-1.9 1.8.5 2.6-2.4-1.3-2.4 1.3.5-2.6-1.9-1.8 2.6-.3z" fill="#fff" stroke="none"/></svg>MY DIARY</a>
    <a href="#"><svg viewBox="0 0 28 28"><path d="M14 1l13 13-13 13L1 14z" fill="#fff"/><path d="M8 12.5h2v3H8zM10 11h2v6h-2zM12 13h4v2h-4zM16 11h2v6h-2zM18 12.5h2v3h-2z" fill="#f37122"/></svg>MY CLUBS</a>
    <a href="#"><svg viewBox="0 0 28 28" fill="#fff"><circle cx="14" cy="8" r="6"/><path d="M3 26v-4c0-4 4-7 8-7h6c4 0 8 3 8 7v4z"/></svg>MY PROFILE</a>
  </aside>

  <main class="content">
    <h1 class="welcome-title">WELCOME TO FITBRISKO</h1>
    <p class="welcome-text">Thanks for visiting! Here are a list of events that we hope are of interest. Just click on the grey tick to join an event, or Login.</p>

    <div class="day-band band-today">TODAY</div>
    <article class="event-card card-1">
      <div class="event-date">Monday 12th September</div>
      <div class="event-thumb thumb-badge" role="img" aria-label="Club crest"></div>
      <div class="event-title">8:15 pm Swim Training</div>
      <div class="event-club">Northfield Striders @ Elmbrook School</div>
      <div class="event-desc">Freestyle (crawl) training comprising of warm up, drills and main set.</div>
    </article>
    <article class="event-card card-2">
      <div class="event-date">Monday 11th September</div>
      <div class="event-thumb thumb-athlete" role="img" aria-label="Photo of an athlete training"></div>
      <div class="event-title">9:15 pm Donec dictum lectus</div>
      <div class="event-club">Northfield Striders @ Elmbrook School</div>
      <div class="event-desc">Freestyle (crawl) training comprising of warm up, drills and main set.</div>
    </article>

    <div class="day-band band-tomorrow">TOMMOROW</div>
    <article class="event-card card-3">
      <div class="event-date">Monday 13th September</div>
      <div class="event-thumb thumb-runner" role="img" aria-label="Photo of a runner at the start line"></div>
      <div class="event-title">10:15 am Fitness Test</div>
      <div class="event-club">Northfield Striders @ Elmbrook School</div>
      <div class="event-desc">Freestyle (crawl) training comprising of warm up, drills and main set.</div>
    </article>
  </main>

  <footer class="site-footer">© 2016 Company Name &nbsp;All right reserved &nbsp;Term of Use</footer>
</body>
</html>
```